Tellmora Corporate Stationery

Look for design of all new corporate stationery for an existing insurance broking business that is going through a redesign and move from older partners to younger family members. New Logo is attached. Company is Brisbane based.
Colours in the Logo is Hex #43bed8 and website features a lot of hex #17b8d8. Website front page "A plan to protect you" - headline. "Professional and Individual advice to protect your greatest assets" - tagline.

Stationery required: Business Cards, Letter head, Thank-you cards, Birthday cards, Presentation folders, With Compliment slips and a powerpoint template. We also would like to send a card to all customers with the something along of the lines of "something new".

Target Market(s)

Customers of Insurance business looking at superannuation, life and income protection insurance, investment advice and wills

Industry/Entity Type

Insurance Broker

Font styles to use
Other font styles liked:
• same as logo

Requirements
Must have
• The above designs for new stationery for the new business including:
• Business Cards, Letter head, Thank-you cards, Birthday cards, Presentation folders, With Compliment slips and a powerpoint template. We also would like to send a card to all customers with the something along of the lines of "something new".
Nice to have
• It is a new look - long time family business being passed to next generation - big focus on advice for YOU, individual advice etc..

```html
<!DOCTYPE html>
<html lang="en">
<head>
<meta charset="utf-8">
<title>Tellmora Business Card</title>
<link href="https://fonts.googleapis.com/css2?family=Open+Sans:wght@400;600;700&display=swap" rel="stylesheet">
<style>
  :root {
    --page-bg: #e9e7e4;
    --card-bg: #f6f7f7;
    --teal: #17b8d8;
    --teal-deep: #1a8fa6;
    --charcoal: #3c3e42;
    --ink: #333639;
    --brand: #43bed8;
  }
  * { margin: 0; padding: 0; box-sizing: border-box; }
  html, body {
    width: 1200px; height: 969px; overflow: hidden;
    background: var(--page-bg);
    font-family: "Open Sans", Arial, sans-serif;
  }
  .business-card {
    position: absolute; left: 100px; top: 200px;
    width: 1000px; height: 568px;
    border-radius: 28px; overflow: hidden;
    background: var(--card-bg);
    box-shadow: 0 18px 40px rgba(0,0,0,0.18);
    color: var(--ink);
  }
  .accent-panel {
    position: absolute; top: 0; right: 0;
    width: 96px; height: 100%;
    background: linear-gradient(180deg, var(--teal) 0%, var(--teal-deep) 70%, var(--charcoal) 100%);
  }
  .brand {
    position: absolute; left: 52px; top: 150px;
    display: flex; align-items: center; gap: 18px;
  }
  .brand-dot {
    width: 44px; height: 44px; border-radius: 50%;
    background: var(--brand);
  }
  .brand-name {
    font-size: 56px; font-weight: 600; color: var(--brand);
    letter-spacing: 1px; line-height: 1;
  }
  .address {
    position: absolute; left: 52px; top: 262px;
    font-size: 24px; line-height: 38px;
  }
  .contact-list {
    position: absolute; left: 58px; top: 348px;
    list-style: none; font-size: 24px;
  }
  .contact-list li {
    display: flex; align-items: center; gap: 14px;
    height: 38px;
  }
  .contact-icon { width: 22px; height: 22px; fill: var(--teal-deep); flex: none; }
  .person {
    position: absolute; right: 130px; top: 188px; text-align: right;
  }
  .person-name {
    font-size: 34px; font-weight: 600; color: var(--teal-deep);
    letter-spacing: 1px; line-height: 44px;
  }
  .person-role { font-size: 26px; line-height: 36px; letter-spacing: 0.5px; }
</style>
</head>
<body>
<div class="business-card">
  <div class="accent-panel" role="img" aria-label="Decorative teal and charcoal accent band"></div>

  <div class="brand">
    <span class="brand-dot"></span>
    <span class="brand-name">TELLMORA</span>
  </div>

  <p class="address">42 Wattle Grove<br>Brisbane, Queensland 4000</p>

  <ul class="contact-list">
    <li><svg class="contact-icon" viewBox="0 0 24 24"><path d="M6.6 10.8a15 15 0 0 0 6.6 6.6l2.2-2.2a1 1 0 0 1 1-.25 11.4 11.4 0 0 0 3.6.57 1 1 0 0 1 1 1V20a1 1 0 0 1-1 1A17 17 0 0 1 3 4a1 1 0 0 1 1-1h3.5a1 1 0 0 1 1 1c0 1.25.2 2.450.57 3.6a1 1 0 0 1-.25 1z"/></svg>07 3184 2260</li>
    <li><svg class="contact-icon" viewBox="0 0 24 24"><path d="M7 1h10a2 2 0 0 1 2 2v18a2 2 0 0 1-2 2H7a2 2 0 0 1-2-2V3a2 2 0 0 1 2-2zm0 3v14h10V4zm5 15.5a1.2 1.2 0 1 0 0 2.4 1.2 1.2 0 0 0 0-2.4z"/></svg>0412 557 903</li>
    <li><svg class="contact-icon" viewBox="0 0 24 24"><path d="M7 2h10v5H7zM4 8h16a2 2 0 0 1 2 2v7h-4v5H6v-5H2v-7a2 2 0 0 1 2-2zm4 8v4h8v-4z"/></svg>07 3184 2261</li>
    <li><svg class="contact-icon" viewBox="0 0 24 24"><path d="M3 5h18a1 1 0 0 1 1 1v12a1 1 0 0 1-1 1H3a1 1 0 0 1-1-1V6a1 1 0 0 1 1-1zm1 2.2V17h16V7.2l-8 5.3z"/></svg>hello@tellmora.example</li>
    <li><svg class="contact-icon" viewBox="0 0 24 24"><path d="M12 2a10 10 0 1 0 0 20 10 10 0 0 0 0-20zm6.9 9h-3a15 15 0 0 0-1.3-5.6A8 8 0 0 1 18.9 11zM12 4.1c.9 1.3 1.7 3.6 1.9 6.9h-3.8c.2-3.3 1-5.6 1.9-6.9zM9.4 5.4A15 15 0 0 0 8.1 11h-3a8 8 0 0 1 4.3-5.6zM5.1 13h3a15 15 0 0 0 1.3 5.6A8 8 0 0 1 5.1 13zm6.9 6.9c-.9-1.3-1.7-3.6-1.9-6.9h3.8c-.2 3.3-1 5.6-1.9 6.9zm2.6-1.3a15 15 0 0 0 1.3-5.6h3a8 8 0 0 1-4.3 5.6z"/></svg>www.tellmora.example</li>
  </ul>

  <div class="person">
    <p class="person-name">LIAM HARCOURT</p>
    <p class="person-role">CEO/FOUNDER</p>
  </div>
</div>
</body>
</html>
```